Harbor Crestline (Business Card Design)

Need business cards designed. Something modern, chic, and sleek. Mabye the back of the card should be the navy blue that is in the logo and then just the logo on the back.

Target Market(s)

Those in the hotel, office, and renovation industry

Contact Information for Business Card

1. Logo 2. Dorian Fenwick 3. CEO/Founder 4. Phone: (833) HarbCre / (833) 427-2731 5. Email: dorian@theharborcrestline.com 6. Website: www.theharborcrestline.com

Font styles to use
Other font styles liked:
• Look at the logo font and base the font for everything else off of that.

Colors
0054AA
0677BA
7BADD7
CADEEF
E8F1F8

Requirements
Must have
• Colors that are associated in the logo
Nice to have
• Sleek modern clean and chic design.

```html
<!DOCTYPE html>
<html lang="en">
<head>
<meta charset="utf-8">
<title>Harbor Crestline – Business Card</title>
<link rel="stylesheet" href="https://fonts.googleapis.com/css2?family=Montserrat:wght@500;700;800&family=Open+Sans:wght@400;600&display=swap">
<style>
  :root {
    --stage: #232323;
    --navy: #0d1840;
    --navy-deep: #0a1236;
    --navy-light: #1f2a66;
    --gold: #d4a94a;
    --white: #ffffff;
  }
  * { box-sizing: border-box; margin: 0; padding: 0; }
  html, body { width: 1200px; height: 780px; overflow: hidden; }
  body {
    background: var(--stage);
    display: flex;
    align-items: center;
    justify-content: center;
    gap: 40px;
    font-family: "Open Sans", sans-serif;
  }
  .card {
    position: relative;
    width: 540px;
    height: 310px;
    border-radius: 22px;
    background: var(--navy);
    border: 3px solid var(--gold);
    overflow: hidden;
  }
  /* Back side */
  .card-back__pattern {
    position: absolute;
    inset: 0;
    background: linear-gradient(200deg, var(--navy-light) 0%, var(--navy) 45%, var(--navy-deep) 100%);
  }
  .wordmark {
    font-family: "Montserrat", sans-serif;
    font-weight: 700;
    color: var(--white);
    letter-spacing: 0.14em;
    text-transform: uppercase;
    display: flex;
    align-items: center;
    gap: 12px;
    line-height: 1;
  }
  .wordmark__square {
    width: 14px; height: 14px;
    background: var(--gold);
    flex: none;
  }
  .card-back .wordmark {
    position: absolute;
    left: 50%; top: 50%;
    transform: translate(-50%, -50%);
    font-size: 30px;
    white-space: nowrap;
  }
  /* Front side */
  .card-front__brand {
    position: absolute;
    left: 0; top: 0;
    width: 270px; height: 250px;
    display: flex;
    align-items: center;
    justify-content: center;
  }
  .card-front__brand .wordmark {
    flex-direction: column;
    gap: 10px;
    font-size: 22px;
    text-align: center;
  }
  .card-front__divider {
    position: absolute;
    left: 278px; top: 40px;
    width: 2px; height: 170px;
    background: var(--white);
  }
  .contact {
    position: absolute;
    left: 300px; top: 40px;
    right: 16px;
    color: var(--white);
  }
  .contact__name {
    font-family: "Montserrat", sans-serif;
    font-weight: 800;
    font-size: 22px;
    line-height: 1.1;
  }
  .contact__name-first { color: var(--gold); }
  .contact__role {
    font-family: "Montserrat", sans-serif;
    font-weight: 700;
    font-size: 12px;
    margin-top: 2px;
  }
  .contact__address {
    font-size: 10px;
    line-height: 1.45;
    margin-top: 14px;
  }
  .contact__list {
    list-style: none;
    margin-top: 12px;
    font-size: 10px;
    line-height: 1.7;
  }
  .contact__list li { display: flex; align-items: center; gap: 6px; white-space: nowrap; }
  .contact__icon { width: 10px; height: 10px; flex: none; }
  .card-front__bands {
    position: absolute;
    left: 0; bottom: 0;
    width: 540px; height: 70px;
  }
</style>
</head>
<body>
  <section class="card card-back" aria-label="Card back">
    <div class="card-back__pattern" role="img" aria-label="Repeating brand pattern fading from light navy to deep navy"></div>
    <div class="wordmark"><span class="wordmark__square"></span><span>Harbor Crestline</span></div>
  </section>

  <section class="card card-front" aria-label="Card front">
    <div class="card-front__brand">
      <div class="wordmark"><span class="wordmark__square"></span><span>Harbor<br>Crestline</span></div>
    </div>
    <div class="card-front__divider"></div>
    <div class="contact">
      <p class="contact__name"><span class="contact__name-first">Dorian</span> Fenwick</p>
      <p class="contact__role">CEO/Founder</p>
      <p class="contact__address">4120 Lantern Ridge Ave<br>Suite 210, Millbrook, MD 21980</p>
      <ul class="contact__list">
        <li>
          <svg class="contact__icon" viewBox="0 0 10 10"><path d="M2 1l2 2-1 1.2a6 6 0 0 0 2.8 2.8L7 6l2 2-1.2 1.2C4.5 9 1 5.5.8 2.2z" fill="#d4a94a"/></svg>
          (833) HarbCre / (833) 427-2731
        </li>
        <li>
          <svg class="contact__icon" viewBox="0 0 10 10"><circle cx="5" cy="5" r="4.2" fill="none" stroke="#d4a94a" stroke-width="1.2"/><path d="M.8 5h8.4M5 .8c-2.4 2.6-2.4 5.8 0 8.4M5 .8c2.4 2.6 2.4 5.8 0 8.4" fill="none" stroke="#d4a94a" stroke-width="0.9"/></svg>
          www.theharborcrestline.com
        </li>
        <li>
          <svg class="contact__icon" viewBox="0 0 10 10"><rect x=".6" y="2" width="8.8" height="6.2" fill="none" stroke="#d4a94a" stroke-width="1.2"/><path d="M.6 2L5 5.6 9.4 2" fill="none" stroke="#d4a94a" stroke-width="1.1"/></svg>
          dorian@theharborcrestline.com
        </li>
      </ul>
    </div>
    <svg class="card-front__bands" viewBox="0 0 540 70" aria-hidden="true">
      <polygon points="0,52 300,52 292,64 0,64" fill="#d4a94a"/>
      <polygon points="330,38 540,38 540,50 322,50" fill="#ffffff"/>
      <rect x="302" y="38" width="18" height="18" fill="#0d1840" stroke="#ffffff" stroke-width="2"/>
    </svg>
  </section>
</body>
</html>
```